4D Cradle Glimpse Luxury Ultrasound Billboard

Design a HIGH-END, MODERN billboard for my private prenatal ultrasound studio, 4D Cradle Glimpse, located in Cedar Bay, FL.
This billboard will be viewed by drivers traveling at highway speeds, so it must be extremely clean, simple, and readable within 6 seconds.
About My Business
4D Cradle Glimpse is a private prenatal ultrasound studio specializing in:
Highest technology 4D/HD Ultrasounds
Early Gender Determination
Pregnancy Confirmation
I have been serving families for nearly 10 years and is known for creating a memorable experience, not just an ultrasound appointment.
Design Style
I DO NOT want:
Flowers
Leaves
Swirls
Glitter
Hearts everywhere
Busy backgrounds
Generic maternity stock graphics
I DO want:
Modern
Luxury
Upscale
Clean
Professional
Eye-catching
Premium medical spa feel
Colors
Use colors from my logo:
LOGO Green ( or a deep green)
Black
White
Soft Gold accents
Images:
Incorporate my professional headshot in a clean, modern way, logo, and the ultrasound images
Text
Keep wording minimal.
Primary Headline ( OPEN TO IDEAS) :
EXAMPLES ( WOULD RATHER SOMETHING MORE CATCHY)
" ADVANCED IMAGING. UNFORGETTABLE MOMENTS"
"MEET YOUR BABY BEFORE BIRTH"
Under headline:
4D Ultrasound • Early Gender • Pregnancy Confirmation
Business Name:
4D Cradle Glimpse
Private Prenatal Ultrasound Studio
Phone Number:
850-471-5923
Important
This billboard must be readable in 5–6 seconds from a moving vehicle.
Less text is better.
The phone number and business name must be visible from a distance.
The design should feel like a premium brand that immediately tells expecting parents:
“This is where I go to see my baby.”
Files Provided
Official logo
Headshot
Ultrasound images
Don’t make this look like a medical office billboard.
Make it look like a luxury baby experience billboard. That’s what separates 4D Cradle Glimpse from hospitals, OB offices, and all the new studios popping up around you. The emotional connection is what gets moms to book. ❤️
Billboard Size - 10.6” x 36”

```html
<!DOCTYPE html>
<html lang="en">
<head>
<meta charset="utf-8">
<title>4D Cradle Glimpse – Billboard</title>
<link rel="stylesheet" href="https://fonts.googleapis.com/css2?family=Jost:wght@400;500&family=Great+Vibes&display=swap">
<style>
  :root {
    --ink: #050505;
    --gold: #e3b44a;
    --gold-soft: #f2cf73;
    --gold-deep: #b8862b;
    --white: #ffffff;
    --sage: #9aa39d;
    --page: #ffffff;
  }
  * { margin: 0; padding: 0; box-sizing: border-box; }
  html, body { width: 1200px; height: 419px; overflow: hidden; background: var(--page); }
  .billboard {
    position: absolute; left: 42px; top: 23px; width: 1116px; height: 349px;
    background: var(--ink); overflow: hidden;
    font-family: "Jost", "Helvetica Neue", Arial, sans-serif;
  }
  .left-field {
    position: absolute; left: 0; top: 31px; width: 614px; height: 318px;
    background: radial-gradient(ellipse at 30% 40%, #1c1c1c 0%, #0a0a0a 70%);
  }
  .gold-waves {
    position: absolute; left: 0; top: 170px; width: 560px; height: 179px;
    background:
      radial-gradient(ellipse 70% 35% at 35% 55%, rgba(227,180,74,0.35) 0%, rgba(227,180,74,0.08) 55%, transparent 75%),
      radial-gradient(ellipse 50% 40% at 10% 20%, rgba(227,180,74,0.25) 0%, transparent 70%);
  }
  .brand-box {
    position: absolute; left: 54px; top: 36px; width: 255px; height: 126px;
    border: 2px solid var(--sage); border-radius: 12px;
    background: linear-gradient(180deg, #1b1c1b 0%, #101110 100%);
    display: flex; flex-direction: column; align-items: center; justify-content: center; gap: 10px;
  }
  .brand-name { display: flex; align-items: center; gap: 8px; color: var(--gold-soft); font-size: 24px; font-weight: 500; }
  .brand-dot { width: 12px; height: 12px; border-radius: 50%; background: var(--gold-soft); }
  .brand-tag { color: var(--white); font-size: 11px; letter-spacing: 0.06em; font-weight: 500; }

  .headline { position: absolute; left: 372px; top: 38px; width: 200px; text-align: center; display: flex; flex-direction: column; align-items: center; }
  .headline-top { color: var(--white); font-size: 41px; font-weight: 400; line-height: 1; white-space: nowrap; }
  .headline-main {
    font-size: 98px; font-weight: 400; line-height: 1; margin-top: 2px; white-space: nowrap;
    background: linear-gradient(180deg, var(--gold-soft), var(--gold-deep));
    -webkit-background-clip: text; background-clip: text; color: transparent;
  }
  .headline-script { font-family: "Great Vibes", cursive; color: var(--white); font-size: 56px; line-height: 1; margin-top: -2px; white-space: nowrap; }

  .scan-frame {
    position: absolute; left: 688px; top: 22px; width: 182px; height: 208px;
    border: 3px solid var(--gold); transform: rotate(3deg);
    background: linear-gradient(135deg, #3a1a14 0%, #8a4a3a 40%, #b06a55 55%, #5a2a20 100%);
  }
  .seal {
    position: absolute; left: 637px; top: 145px; width: 90px; height: 90px; border-radius: 50%;
    background: radial-gradient(circle at 40% 35%, var(--gold-soft), var(--gold-deep));
    border: 2px solid #f5dc95;
    display: flex; flex-direction: column; align-items: center; justify-content: center; color: var(--ink);
  }
  .seal-script { font-family: "Great Vibes", cursive; font-size: 17px; line-height: 1; }
  .seal-text { font-size: 8.5px; font-weight: 500; line-height: 1.25; text-align: center; letter-spacing: 0.04em; }

  .portrait-arc { position: absolute; left: 880px; top: 0; width: 236px; height: 300px; }
  .portrait {
    position: absolute; left: 932px; top: 26px; width: 162px; height: 230px;
    background: linear-gradient(180deg, #d8c08a 0%, #c9a27e 35%, #3e5a3c 65%, #2f4630 100%);
    border-radius: 70px 70px 6px 6px;
  }

  .services { position: absolute; left: 616px; top: 258px; color: var(--white); font-size: 11.5px; font-weight: 500; letter-spacing: 0.02em; white-space: nowrap; }
  .rule { position: absolute; left: 385px; top: 282px; width: 731px; height: 1px; background: var(--gold-deep); }

  .contact { position: absolute; top: 298px; height: 36px; display: flex; align-items: center; font-weight: 400; white-space: nowrap; }
  .contact .dash { width: 22px; height: 1px; background: var(--gold); }
  .location { left: 390px; gap: 9px; color: var(--gold); font-size: 23px; }
  .divider { position: absolute; left: 683px; top: 298px; width: 1px; height: 36px; background: var(--gold-deep); }
  .call { left: 710px; gap: 16px; color: var(--gold); font-size: 23px; }
  .phone { color: var(--white); font-size: 26px; font-weight: 500; }
</style>
</head>
<body>
  <div class="billboard">
    <div class="left-field"></div>
    <div class="gold-waves" role="img" aria-label="Soft flowing gold light accents"></div>

    <div class="brand-box">
      <div class="brand-name"><span class="brand-dot"></span>4D Cradle Glimpse</div>
      <div class="brand-tag">PRENATAL ULTRASOUND STUDIO</div>
    </div>

    <div class="headline">
      <div class="headline-top">MEET YOUR</div>
      <div class="headline-main">BABY</div>
      <div class="headline-script">Before Birth</div>
    </div>

    <div class="scan-frame" role="img" aria-label="4D ultrasound image of twin babies"></div>
    <div class="seal">
      <span class="seal-script">Cherish</span>
      <span class="seal-text">EVERY<br>MOMENT</span>
    </div>

    <svg class="portrait-arc" viewBox="0 0 236 300" aria-hidden="true">
      <path d="M138 15 A131 131 0 0 0 110 275" fill="none" stroke="#e3b44a" stroke-width="3"/>
    </svg>
    <div class="portrait" role="img" aria-label="Professional headshot of the studio owner"></div>

    <div class="services">4D ULTRASOUND · EARLY GENDER · PREGNANCY</div>
    <div class="rule"></div>

    <div class="contact location">
      <span class="dash"></span>
      <svg width="18" height="24" viewBox="0 0 18 24" aria-hidden="true">
        <path d="M9 0C4 0 0 4 0 9c0 6.5 9 15 9 15s9-8.5 9-15c0-5-4-9-9-9zm0 12.5a3.5 3.5 0 1 1 0-7 3.5 3.5 0 0 1 0 7z" fill="#e3b44a"/>
      </svg>
      <span>CEDAR BAY, FL</span>
      <span class="dash"></span>
    </div>
    <div class="divider"></div>
    <div class="contact call">
      <span>CALL NOW</span>
      <span class="dash"></span>
      <span class="phone">850-471-5923</span>
      <svg width="22" height="22" viewBox="0 0 24 24" aria-hidden="true">
        <path d="M6.6 10.8c1.4 2.8 3.8 5.1 6.6 6.6l2.2-2.2c.3-.3.7-.4 1-.2 1.1.4 2.3.6 3.6.6.6 0 1 .4 1 1V20c0 .6-.4 1-1 1C10.6 21 3 13.4 3 4c0-.6.4-1 1-1h3.5c.6 0 1 .4 1 1 0 1.3.2 2.5.6 3.6.1.3 0 .7-.2 1L6.6 10.8z" fill="#e3b44a"/>
        <path d="M15 3.5a6 6 0 0 1 5.5 5.5M15 7a2.5 2.5 0 0 1 2 2" fill="none" stroke="#e3b44a" stroke-width="1.6" stroke-linecap="round"/>
      </svg>
    </div>
  </div>
</body>
</html>
```